Harcourt Power Gym Chronic Pain Flyer

Double sided DL flyer required to promote a strength training studio to sufferers of chronic pain. Flyer will be displayed in osteopathy, chiropractic and massage clinics. Flyer should be clean, professional and appeal to an older (40+) demographic.

Target Market(s)

Chronic pain sufferers. Age 40+

Industry/Entity Type

Health And Wellness

Colors

Designer to choose colors to be used in the design.

Requirements
Must have
• See attached files for text copy and logo. Image(s) of people strength training with a coach or personal trainer, as well as images depicting pain in common parts of the body (such as those pictured in the supplied mock up)
• website address: harcourtpowergym.com.au
• phone number : 0458 214 963
• Street address: 3/14 Birchwood Rd, Harcourt
Nice to have
• Images such as in the attached files.

```html
<!DOCTYPE html>
<html lang="en">
<head>
<meta charset="utf-8">
<title>Harcourt Power Gym – Chronic Pain Flyer</title>
<link href="https://fonts.googleapis.com/css2?family=Lato:wght@400;700;900&display=swap" rel="stylesheet">
<style>
  :root {
    --stage: #3a3a3a;
    --red: #d21f27;
    --ink: #111111;
    --grey-dark: #555555;
    --white: #ffffff;
    --paper: #fafafa;
  }
  * { box-sizing: border-box; margin: 0; padding: 0; }
  html, body { width: 1200px; height: 1200px; overflow: hidden; }
  body { background: var(--stage); font-family: "Lato", sans-serif; position: relative; }
  .flyer { position: absolute; background: var(--white); overflow: hidden; box-shadow: 0 4px 14px rgba(0,0,0,0.45); }
  .flyer-front { left: 128px; top: 128px; width: 441px; height: 908px; }
  .flyer-back  { left: 637px; top: 127px; width: 443px; height: 912px; background: var(--paper); }
  .flyer svg.shapes { position: absolute; left: 0; top: 0; }
  .layer { position: absolute; left: 0; width: 100%; text-align: center; }

  .brand-name {
    font-weight: 900; color: var(--grey-dark); letter-spacing: 1px; font-size: 26px;
    text-transform: uppercase; display: flex; align-items: center; justify-content: center; gap: 10px;
  }
  .brand-dot { width: 16px; height: 16px; border-radius: 50%; background: var(--red); }

  .headline-small { font-weight: 700; font-size: 43px; line-height: 1; letter-spacing: -0.5px; white-space: nowrap; }
  .headline-big { font-weight: 900; font-size: 75px; line-height: 1; letter-spacing: -0.5px; white-space: nowrap; }
  .flyer-front .headline-small, .flyer-front .headline-big { color: var(--white); }
  .flyer-back .headline-small, .flyer-back .headline-big { color: var(--ink); }

  .contact-phone { font-weight: 900; font-size: 38px; line-height: 1; display: flex; align-items: center; justify-content: center; gap: 6px; }
  .contact-line { font-size: 18px; line-height: 1; display: flex; align-items: center; justify-content: center; gap: 12px; }
  .flyer-front .contact-phone { color: var(--red); }
  .flyer-front .contact-line { color: var(--ink); }
  .flyer-back .contact-phone, .flyer-back .contact-line { color: var(--white); }

  .tagline-band {
    position: absolute; left: 0; top: 167px; width: 100%; height: 47px;
    background: var(--red); color: var(--white);
    font-weight: 700; font-size: 28px; line-height: 47px; text-align: center;
  }
  .body-copy {
    position: absolute; left: 26px; right: 26px; font-size: 20.5px; line-height: 25px; color: var(--ink);
    text-align: justify; text-align-last: left;
  }
  .pain-spot {
    position: absolute; width: 124px; height: 124px; border-radius: 50%; border: 2px solid var(--red);
    background: radial-gradient(ellipse 45% 35% at 50% 60%, #ef5a62 0%, #f2a3a6 35%, rgba(200,200,200,0) 70%),
                linear-gradient(160deg, #ececec 0%, #9d9d9d 55%, #d6d6d6 100%);
  }
  .side-label { position: absolute; top: 1076px; color: var(--white); font-size: 38px; font-weight: 400; width: 200px; text-align: center; }
</style>
</head>
<body>

<section class="flyer flyer-front">
  <svg class="shapes" width="441" height="908" viewBox="0 0 441 908">
    <defs>
      <linearGradient id="coachTones" x1="0" y1="0" x2="1" y2="1">
        <stop offset="0" stop-color="#6f7c84"/>
        <stop offset="0.35" stop-color="#d9b4a4"/>
        <stop offset="0.6" stop-color="#c9cdd0"/>
        <stop offset="1" stop-color="#4f6570"/>
      </linearGradient>
    </defs>
    <rect role="img" aria-label="Photo: a female coach helping an older man with a strength exercise in the gym" x="0" y="150" width="441" height="460" fill="url(#coachTones)"/>
    <path d="M0,0 H441 V150 Q220,214 0,160 Z" fill="#ffffff"/>
    <path d="M0,160 Q220,214 441,150 L441,157 Q220,222 0,166 Z" fill="#a9a9a9"/>
    <path d="M0,530 Q220,625 441,530 L441,560 Q220,640 0,560 Z" fill="#b3b3b3"/>
    <path d="M0,550 Q220,640 441,550 L441,758 L0,758 Z" fill="var(--red)"/>
    <rect x="0" y="884" width="441" height="24" fill="var(--red)"/>
  </svg>

  <div class="layer brand-name" style="top:72px;"><span class="brand-dot"></span>Harcourt Power Gym</div>

  <div class="layer headline-small" style="top:624px;">HEALTH THROUGH</div>
  <div class="layer headline-big" style="top:666px;">STRENGTH</div>

  <div class="layer contact-phone" style="top:771px;">
    <svg width="38" height="38" viewBox="0 0 38 38"><circle cx="19" cy="19" r="17" fill="none" stroke="#888" stroke-width="2"/><path d="M13,10 l4,0 l2,5 l-3,2 q2,4 6,6 l2,-3 l5,2 l0,4 q-1,2 -4,2 q-14,-2 -14,-15 q0,-3 2,-3z" fill="#888"/></svg>
    <span>0458 214 963</span>
  </div>
  <div class="layer contact-line" style="top:821px;">
    <svg width="20" height="20" viewBox="0 0 20 20" fill="none" stroke="#888" stroke-width="1.4"><circle cx="10" cy="10" r="8.5"/><ellipse cx="10" cy="10" rx="3.8" ry="8.5"/><path d="M1.5,10 H18.5 M3,5.5 H17 M3,14.5 H17"/></svg>
    <span>harcourtpowergym.com.au</span>
  </div>
  <div class="layer contact-line" style="top:855px;">
    <svg width="14" height="20" viewBox="0 0 14 20"><path d="M7,0 a7,7 0 0 1 7,7 c0,5 -7,13 -7,13 s-7,-8 -7,-13 a7,7 0 0 1 7,-7z" fill="#888"/><circle cx="7" cy="7" r="2.6" fill="#fff"/></svg>
    <span>3/14 Birchwood Rd, Harcourt</span>
  </div>
</section>

<section class="flyer flyer-back">
  <svg class="shapes" width="443" height="912" viewBox="0 0 443 912">
    <path d="M0,678 Q221,790 443,678 L443,710 Q221,800 0,710 Z" fill="#a9a9a9"/>
    <path d="M0,705 Q221,800 443,705 L443,912 L0,912 Z" fill="var(--red)"/>
  </svg>

  <div class="layer headline-small" style="top:33px;">HEALTH THROUGH</div>
  <div class="layer headline-big" style="top:76px;">STRENGTH</div>

  <div class="tagline-band">You Don’t have to live in pain.</div>

  <p class="body-copy" style="top:227px;">Strength training has been shown to improve many chronic pain conditions and is now being routinely recommended by medical and health professionals.</p>

  <div class="pain-spot" role="img" aria-label="Photo: lower back pain highlighted in red" style="left:14px; top:342px;"></div>
  <div class="pain-spot" role="img" aria-label="Photo: shoulder pain highlighted in red" style="left:156px; top:342px;"></div>
  <div class="pain-spot" role="img" aria-label="Photo: knee pain highlighted in red" style="left:297px; top:342px;"></div>

  <p class="body-copy" style="top:487px;">Our private studio provides high quality strength training by expert strength coaches. We’ve helped countless people improve or eliminate chronic pain, contact us today and find out how we can help you.</p>

  <div class="layer brand-name" style="top:664px;"><span class="brand-dot"></span>Harcourt Power Gym</div>

  <div class="layer contact-phone" style="top:775px;">
    <svg width="38" height="38" viewBox="0 0 38 38"><circle cx="19" cy="19" r="17" fill="none" stroke="#fff" stroke-width="2"/><path d="M13,10 l4,0 l2,5 l-3,2 q2,4 6,6 l2,-3 l5,2 l0,4 q-1,2 -4,2 q-14,-2 -14,-15 q0,-3 2,-3z" fill="#fff"/></svg>
    <span>0458 214 963</span>
  </div>
  <div class="layer contact-line" style="top:823px;">
    <svg width="20" height="20" viewBox="0 0 20 20" fill="none" stroke="#fff" stroke-width="1.4"><circle cx="10" cy="10" r="8.5"/><ellipse cx="10" cy="10" rx="3.8" ry="8.5"/><path d="M1.5,10 H18.5 M3,5.5 H17 M3,14.5 H17"/></svg>
    <span>harcourtpowergym.com.au</span>
  </div>
  <div class="layer contact-line" style="top:850px;">
    <svg width="14" height="20" viewBox="0 0 14 20"><path d="M7,0 a7,7 0 0 1 7,7 c0,5 -7,13 -7,13 s-7,-8 -7,-13 a7,7 0 0 1 7,-7z" fill="#fff"/><circle cx="7" cy="7" r="2.6" fill="var(--red)"/></svg>
    <span>3/14 Birchwood Rd, Harcourt</span>
  </div>
</section>

<div class="side-label" style="left:226px;">Front</div>
<div class="side-label" style="left:745px;">Back</div>

</body>
</html>
```